NZ First of it's kind solutions directory and marketplace for busy Mums needs a business card design

We need a business card design for our new nationwide business in NZ (long term plans to go global). We provide solutions to the everyday challenges that busy Mums face by connecting them with quality communities and suppliers of carefully selected, relevant products and services. We sell direct via our online marketplace. The final design should communicate our values of inclusivity, quality and smart solutions. Colours should incorporate our logo colour palette of #477077 and #6ba8b2. Our website is at https://www.brightnestmums.example

Target Market(s)

busy Mums, Age 28 – 50, female, income over $100K, location main centres NZ primarily but NZ wide. Is likely juggling work or career with a young family. Probably had hobbies which have fallen by the wayside.
-Wants to succeed in her chosen career without compromising on family life
-to successfully juggle her career without feeling like she is compromising her children
- Is time poor, something always has to give and it’s generally her health (she’ll stay up late, get stressed)
- probably ex corporate or professional career. Has discretional income

Industry/Entity Type

Business

Contact Information for Business Card

Lena Forbisher, Founder, BrightNestMums.example (Strapline Tap; Gather; Sorted), 47 Kowhai Terrace, Ellerslie, Auckland 1051, New Zealand. Mob: 021 483 517 Ph: +64 (0)9 571 4860

Font styles to use
Other font styles liked:
• Raleway, and/or Architects Daughter

Colors
00a990
33b8a4
86cfc6
cfeae6

Requirements
Must have
• the above details, streamline. the logo and colours associated with those logos
Should not have
• foil or metallic colours

```html
<!DOCTYPE html>
<html lang="en">
<head>
<meta charset="utf-8">
<title>BrightNestMums Business Card</title>
<link rel="stylesheet" href="https://fonts.googleapis.com/css2?family=Raleway:wght@400;500;700;800&display=swap">
<style>
  :root {
    --teal-dark: #477077;
    --teal-light: #6ba8b2;
    --white: #ffffff;
    --stage: #2a2a2c;
  }
  html, body {
    margin: 0;
    padding: 0;
    width: 1200px;
    height: 880px;
    overflow: hidden;
    background: var(--stage);
    font-family: "Raleway", sans-serif;
  }
  .canvas {
    position: relative;
    width: 1200px;
    height: 880px;
  }
  .card {
    position: absolute;
    width: 600px;
    height: 343px;
    border-radius: 22px;
    overflow: hidden;
    box-shadow: 0 10px 30px rgba(0,0,0,0.45);
  }
  /* Back of card */
  .card-back {
    left: 80px;
    top: 70px;
    background: linear-gradient(180deg, var(--teal-light) 0%, var(--teal-dark) 100%);
    color: var(--white);
    display: flex;
    flex-direction: column;
    align-items: center;
    justify-content: center;
  }
  .brand {
    display: flex;
    align-items: center;
    gap: 14px;
  }
  .brand-dot {
    width: 34px;
    height: 34px;
    border-radius: 50%;
    background: currentColor;
  }
  .brand-name {
    font-weight: 800;
    font-size: 44px;
    letter-spacing: -1px;
  }
  .card-back .website {
    margin-top: 14px;
    font-size: 15px;
    letter-spacing: 1.5px;
    font-weight: 500;
  }
  /* Front of card */
  .card-front {
    left: 520px;
    top: 460px;
    background: var(--white);
  }
  .card-front .wave {
    position: absolute;
    inset: 0;
  }
  .card-front .brand {
    position: absolute;
    left: 46px;
    top: 66px;
    color: var(--teal-dark);
  }
  .card-front .brand-name { font-size: 44px; }
  .person {
    position: absolute;
    left: 150px;
    top: 222px;
    color: var(--white);
  }
  .person-name {
    font-weight: 800;
    font-size: 18px;
    line-height: 20px;
    margin: 0;
  }
  .person-title {
    font-size: 13px;
    line-height: 16px;
    margin: 0 0 6px;
  }
  .contact-list {
    list-style: none;
    margin: 0;
    padding: 0;
    font-size: 13px;
    line-height: 18px;
  }
  .contact-list li {
    display: flex;
    align-items: center;
    gap: 8px;
  }
  .contact-icon {
    width: 14px;
    height: 14px;
  }
  .address {
    position: absolute;
    right: 28px;
    top: 172px;
    text-align: right;
    color: var(--white);
    font-size: 14px;
    line-height: 18px;
    font-style: normal;
  }
</style>
</head>
<body>
<main class="canvas">
  <section class="card card-back" aria-label="Business card back">
    <div class="brand">
      <span class="brand-dot"></span>
      <span class="brand-name">BrightNestMums</span>
    </div>
    <div class="website">www.brightnestmums.example</div>
  </section>

  <section class="card card-front" aria-label="Business card front">
    <svg class="wave" viewBox="0 0 600 343" preserveAspectRatio="none" aria-hidden="true">
      <path d="M565,0 L600,0 L600,72 C585,82 560,95 528,108 C590,70 595,30 565,0 Z" fill="var(--teal-light)"/>
      <path d="M0,248 C120,200 300,168 450,136 C520,120 565,95 600,75 L600,92 C570,108 520,126 450,142 C300,176 120,212 0,262 Z" fill="var(--teal-light)"/>
      <path d="M0,270 C120,220 300,185 450,150 C520,134 570,115 600,100 L600,343 L0,343 Z" fill="var(--teal-dark)"/>
    </svg>

    <div class="brand">
      <span class="brand-dot"></span>
      <span class="brand-name">BrightNestMums</span>
    </div>

    <div class="person">
      <p class="person-name">Lena Forbisher</p>
      <p class="person-title">Founder</p>
      <ul class="contact-list">
        <li>
          <svg class="contact-icon" viewBox="0 0 16 16" aria-hidden="true"><circle cx="8" cy="8" r="7" fill="none" stroke="#fff" stroke-width="1.2"/><rect x="5.5" y="3.5" width="5" height="9" rx="1" fill="none" stroke="#fff" stroke-width="1.1"/></svg>
          021 483 517
        </li>
        <li>
          <svg class="contact-icon" viewBox="0 0 16 16" aria-hidden="true"><circle cx="8" cy="8" r="7" fill="none" stroke="#fff" stroke-width="1.2"/><path d="M4.5,6 C4.5,4.5 11.5,4.5 11.5,6 L10.5,7 L9.5,6.2 L6.5,6.2 L5.5,7 Z M5,11 L11,11 L10,8 L6,8 Z" fill="#fff"/></svg>
          +64 (0)9 571 4860
        </li>
        <li>
          <svg class="contact-icon" viewBox="0 0 16 16" aria-hidden="true"><circle cx="8" cy="8" r="7" fill="none" stroke="#fff" stroke-width="1.2"/><circle cx="8" cy="8" r="4.5" fill="none" stroke="#fff" stroke-width="1"/><path d="M3.5,8 H12.5 M8,3.5 V12.5" stroke="#fff" stroke-width="0.9"/></svg>
          www.brightnestmums.example
        </li>
      </ul>
    </div>

    <address class="address">
      47 Kowhai Terrace,<br>
      Ellerslie, Auckland 1051<br>
      New Zealand
    </address>
  </section>
</main>
</body>
</html>
```